New business card/stationary for a consulting company

I am looking for a clean and very professional looking business card for my consulting company as well as corresponding stationary. I am uploading our logo. I like simple and powerful for the feel. No graphics but I am open on everything else. Below is my contact information but would like the final to be in a version I can add my employees information into and print. Thank you.

Daniel Whitcombe
dan@ferncliffadvisory.com
2870 North 9th Avenue, Summit Floor, Elm Ridge, Illinois 60531
www.ferncliffadvisory.com

Industry/Entity Type

Consulting

Contact Information for Business Card

Daniel Whitcombe
dan@ferncliffadvisory.com
www.ferncliffadvisory.com

Font styles to use
Serif
Sans Serif

Requirements
Must have
• Our logo and the business card details.
Nice to have
• our website www.ferncliffadvisory.com

```html
<!DOCTYPE html>
<html lang="en">
<head>
<meta charset="utf-8">
<title>Ferncliff Advisory – Business Card</title>
<link rel="stylesheet" href="https://fonts.googleapis.com/css2?family=Cinzel:wght@700&family=Questrial&family=Roboto:wght@400&display=swap">
<style>
  :root {
    --backdrop: #e9e6e1;
    --card-paper: #f4f4f4;
    --navy: #0a0a78;
    --navy-bright: #0b0b9c;
    --navy-deep: #05055e;
    --ink-grey: #555555;
    --divider: #bdbdbd;
    --white: #ffffff;
  }
  * { margin: 0; padding: 0; box-sizing: border-box; }
  html, body {
    width: 1200px;
    height: 960px;
    overflow: hidden;
    background: var(--backdrop);
  }
  .canvas {
    position: relative;
    width: 1200px;
    height: 960px;
  }

  /* Front of card */
  .card-front {
    position: absolute;
    left: 302px;
    top: 130px;
    width: 600px;
    height: 341px;
    background: var(--card-paper);
    border-bottom: 6px solid var(--navy);
    box-shadow: 0 2px 6px rgba(0,0,0,0.25);
  }
  .front-brand {
    position: absolute;
    left: 0;
    top: 136px;
    width: 332px;
    text-align: center;
  }
  .brand-square {
    display: block;
    width: 22px;
    height: 22px;
    margin: 0 auto 12px;
    background: var(--navy);
  }
  .brand-name {
    font-family: "Questrial", sans-serif;
    font-size: 20px;
    letter-spacing: 0.5px;
    color: var(--navy);
    text-transform: uppercase;
    white-space: nowrap;
  }
  .front-divider {
    position: absolute;
    left: 316px;
    top: 104px;
    width: 1px;
    height: 136px;
    background: linear-gradient(to bottom, transparent, var(--divider) 20%, var(--divider) 80%, transparent);
  }
  .contact-block {
    position: absolute;
    left: 345px;
    top: 102px;
  }
  .person-name {
    font-family: "Cinzel", serif;
    font-weight: 700;
    font-size: 17px;
    letter-spacing: 0.8px;
    color: var(--navy);
    margin-bottom: 10px;
  }
  .postal-address,
  .contact-line {
    font-family: "Roboto", sans-serif;
    font-size: 14px;
    line-height: 18px;
    color: var(--ink-grey);
    font-style: normal;
  }
  .postal-address { margin-bottom: 8px; }
  .contact-line {
    display: flex;
    align-items: center;
    gap: 6px;
  }
  .contact-icon { width: 13px; height: 13px; flex: none; }

  /* Back of card */
  .card-back {
    position: absolute;
    left: 299px;
    top: 488px;
    width: 600px;
    height: 343px;
    background: linear-gradient(100deg, var(--navy-bright) 0%, #08088a 50%, var(--navy-deep) 100%);
    box-shadow: 0 2px 6px rgba(0,0,0,0.3);
  }
  .back-brand {
    position: absolute;
    left: 0;
    top: 118px;
    width: 100%;
    text-align: center;
  }
  .back-brand .brand-square {
    width: 40px;
    height: 40px;
    margin-bottom: 26px;
    background: var(--white);
  }
  .back-brand .brand-name {
    font-size: 32px;
    color: var(--white);
  }
</style>
</head>
<body>
<main class="canvas">
  <section class="card-front" aria-label="Business card front">
    <div class="front-brand">
      <span class="brand-square"></span>
      <p class="brand-name">Ferncliff Advisory</p>
    </div>
    <div class="front-divider"></div>
    <div class="contact-block">
      <h1 class="person-name">Daniel Whitcombe</h1>
      <address class="postal-address">
        2870 North 9th Avenue<br>
        Summit Floor, Elm Ridge<br>
        Illinois 60531
      </address>
      <p class="contact-line">
        <svg class="contact-icon" viewBox="0 0 13 13" aria-hidden="true">
          <rect x="0.5" y="2.5" width="12" height="8" fill="var(--navy)"/>
          <path d="M0.8 3 L6.5 7.2 L12.2 3" fill="none" stroke="#fff" stroke-width="1"/>
        </svg>
        dan@ferncliffadvisory.com
      </p>
      <p class="contact-line">
        <svg class="contact-icon" viewBox="0 0 13 13" aria-hidden="true">
          <circle cx="6.5" cy="6.5" r="6" fill="var(--navy)"/>
          <ellipse cx="6.5" cy="6.5" rx="2.4" ry="6" fill="none" stroke="#fff" stroke-width="0.9"/>
          <line x1="0.5" y1="6.5" x2="12.5" y2="6.5" stroke="#fff" stroke-width="0.9"/>
        </svg>
        www.ferncliffadvisory.com
      </p>
    </div>
  </section>

  <section class="card-back" aria-label="Business card back">
    <div class="back-brand">
      <span class="brand-square"></span>
      <p class="brand-name">Ferncliff Advisory</p>
    </div>
  </section>
</main>
</body>
</html>
```